Youth organisation needs design work for awards booklet

We are from The Harbour Crew in Singapore, and we need design work for an awards booklet for one of our most prestigious awards, the Keystone Award. This booklet will comprise of the list of the recipients, congratulatory notes and stories from some of the recipients. This booklet will be printed for each of the recipient to keep as a remembrance. We are looking for dual or tri-colour scheme, with bronze being one of the colours.

Target Market(s)

Recipients of the Award, school Principals and teachers

Requirements
Must have
• We are looking to have around 16 designed pages, including front and back cover. Size of the booklet is:
Closed - W100mm x H210mm; Opened - W200mm x H210mm
Cover page - picture of the Award
Page 2-3 - two congratulatory notes
Page 4-5 - picture of the Award and description of the Award
Page 6-7 - Testimonials
Page 8-14 - List of recipients (to be provided upon confirmation of designer)
Page 15 - blank page or acknowledgments page
Back Cover - HC Logo and contact details
(Refer to previous years' booklets for reference)

Designers can submit just the cover pages as well as 1 sample inner page to get a sense of the overall style of design during the selection round.
Nice to have
• Clean, prestigious/premium look

```html
<!DOCTYPE html>
<html lang="en">
<head>
<meta charset="utf-8">
<title>Keystone Award – Presentation Ceremony Booklet</title>
<link rel="stylesheet" href="https://fonts.googleapis.com/css2?family=Anton&family=Dancing+Script:wght@500&family=Montserrat:wght@600;700&family=Open+Sans:wght@600&family=Roboto+Condensed:ital,wght@0,400;0,700;1,400&display=swap">
<style>
:root{
  --paper:#f3f0eb;
  --brown-dark:#3d140c;
  --brown:#6e2c16;
  --brown-mid:#8a3a1a;
  --gold:#d9b04a;
  --gold-light:#f1d77e;
  --gold-deep:#b8862a;
  --maroon:#8a1c2a;
  --cream:#fff3d6;
  --teal:#1a98a8;
  --yellow:#f7e23a;
  --card:#d8ec9a;
  --blob-blue:#3a8fc2;
  --blob-sky:#a9d6ea;
  --blob-lime:#e2eb7a;
  --blob-green:#c4e58a;
  --ink:#3a1a12;
}
*{box-sizing:border-box;margin:0;padding:0}
html,body{width:1200px;height:3881px;overflow:hidden}
body{background:var(--paper);position:relative;font-family:"Roboto Condensed",sans-serif;color:var(--ink)}

.sparkle{
  background:
    radial-gradient(circle at 78% 28%,rgba(255,170,40,.45),transparent 32%),
    radial-gradient(circle at 22% 72%,rgba(255,150,30,.32),transparent 30%),
    radial-gradient(circle at 60% 85%,rgba(255,190,60,.28),transparent 25%),
    linear-gradient(160deg,var(--brown-dark),var(--brown-mid) 50%,var(--brown-dark));
}

/* Cover pages */
.cover{position:absolute;width:380px;height:798px;overflow:hidden;box-shadow:0 10px 30px rgba(0,0,0,.18)}
.front-cover{left:410px;top:60px}
.back-cover{left:410px;top:2840px}
.cover svg.waves{position:absolute;inset:0}
.tilt{position:absolute;transform:rotate(-12deg);transform-origin:left top}

.cover-title{left:70px;top:110px;text-align:center;width:240px}
.cover-title h1{font-family:"Anton",sans-serif;font-weight:400;color:var(--maroon);font-size:44px;line-height:1;letter-spacing:.5px;-webkit-text-stroke:1px #fff;text-transform:uppercase}
.cover-title p{font-family:"Open Sans",sans-serif;font-weight:600;color:var(--cream);font-size:19px;margin-top:8px}

.medal{position:absolute;left:88px;top:330px;width:170px;height:190px;border-radius:50%;
  background:radial-gradient(circle at 40% 35%,#f2e6c4,#b59a5e 55%,#6d5a34);}

.cover-info{left:60px;top:600px;color:var(--cream);font-family:"Open Sans",sans-serif;font-weight:600;text-align:center;width:250px}
.cover-info .guest{font-size:15px;margin-bottom:54px}
.cover-info .venue{font-size:15px;line-height:1.25;text-transform:uppercase;margin-bottom:18px}
.cover-info .date{font-size:15px}

.back-contact{left:60px;top:640px;color:var(--ink);font-size:12px;line-height:1.35}
.brand{display:flex;align-items:center;gap:8px;margin-bottom:8px}
.brand-dot{width:26px;height:26px;border-radius:50%;background:var(--maroon)}
.brand-name{font-family:"Roboto Condensed",sans-serif;font-weight:700;font-size:15px;color:var(--maroon);text-transform:uppercase}

/* Spreads */
.spread{position:absolute;left:200px;width:800px;height:840px;overflow:hidden;box-shadow:0 12px 34px rgba(0,0,0,.2)}
.spread-testimonials{top:960px}
.spread-recipients{top:1900px}
.spread::after{content:"";position:absolute;left:398px;top:0;width:4px;height:100%;background:linear-gradient(90deg,rgba(0,0,0,.25),rgba(255,255,255,.08))}

.blob{position:absolute;display:flex;align-items:center;justify-content:center;text-align:center;padding:40px 46px;font-size:11.5px;line-height:1.25;color:#fff}
.blob-1{left:35px;top:105px;width:362px;height:307px;background:var(--blob-blue);border-radius:60% 40% 45% 55% / 55% 45% 55% 45%}
.blob-2{left:19px;top:514px;width:369px;height:298px;background:var(--blob-sky);color:var(--maroon);border-radius:40% 60% 50% 50% / 60% 55% 45% 40%}
.blob-3{left:420px;top:27px;width:369px;height:330px;background:var(--blob-lime);color:var(--maroon);border-radius:45% 55% 60% 40% / 40% 60% 40% 60%}
.blob-4{left:420px;top:435px;width:369px;height:377px;background:var(--blob-green);color:var(--ink);border-radius:55% 45% 40% 60% / 45% 55% 45% 55%}

.section-title{position:absolute;text-align:center}
.section-title h2{font-family:"Anton",sans-serif;font-weight:400;color:var(--maroon);-webkit-text-stroke:1.5px #fff;line-height:1}
.section-title .kicker{font-family:"Montserrat",sans-serif;font-weight:700;color:#fff;letter-spacing:6px;text-transform:uppercase}
.testimonials-title{left:20px;top:425px;width:360px}
.testimonials-title h2{font-size:50px}
.testimonials-title .kicker{font-size:19px;margin-top:4px}

.recipients-title{left:20px;top:40px;width:360px}
.recipients-title h2{font-size:40px}
.recipients-title .kicker{font-size:19px;margin-top:8px}
.recipients-title .lead{font-family:"Dancing Script",cursive;color:#fff;font-size:21px;line-height:1.3;margin-top:14px}

.company{position:absolute;width:340px;height:165px;background:var(--card);padding:14px 14px 0 14px;
  clip-path:polygon(0 0,calc(100% - 24px) 0,100% 24px,100% 100%,0 100%);border-radius:0 0 10px 10px}
.company-wrap{position:absolute;width:340px;height:165px}
.company-no{position:absolute;left:-14px;top:-12px;width:54px;height:54px;border-radius:50%;background:var(--teal);z-index:2;
  display:flex;align-items:baseline;justify-content:center;padding-top:4px;color:var(--yellow);font-family:"Anton",sans-serif;font-size:34px;line-height:1.1}
.company-no small{font-family:"Montserrat",sans-serif;font-size:14px;font-weight:700}
.company h3{font-family:"Montserrat",sans-serif;font-weight:700;color:var(--maroon);font-size:19px;margin-left:42px;line-height:1.1}
.company .unit{font-style:italic;font-size:12.5px;text-align:center;line-height:1.35;margin-top:8px;color:var(--ink)}
.company ul{list-style:none;font-weight:700;font-size:12px;line-height:1.35}
.roster{display:flex;gap:24px;margin-top:10px;padding-left:4px}
</style>
</head>
<body>

<!-- Front cover -->
<section class="cover front-cover sparkle" role="img" aria-label="Front cover with warm brown background and golden glitter sparkles">
  <svg class="waves" width="380" height="798" viewBox="0 0 380 798" aria-hidden="true">
    <path d="M0 70 L170 0 L380 0 L380 250 Q210 300 0 395 Z" fill="var(--gold)"/>
    <path d="M120 0 L250 0 Q160 150 0 260 L0 200 Q90 110 120 0 Z" fill="var(--gold-light)" opacity=".55"/>
    <path d="M0 395 Q210 300 380 250 L380 270 Q210 320 0 418 Z" fill="var(--gold-deep)" opacity=".7"/>
  </svg>
  <div class="tilt cover-title">
    <h1>The<br>Keystone<br>Award</h1>
    <p>Presentation Ceremony</p>
  </div>
  <div class="medal" role="img" aria-label="Photograph of the Keystone Award medal"></div>
  <div class="tilt cover-info">
    <p class="guest">Guest-of-Honour</p>
    <p class="venue">Grand Ballroom<br>Lantern Bay Club</p>
    <p class="date">XX Month 2020</p>
  </div>
</section>

<!-- Testimonials spread -->
<section class="spread spread-testimonials sparkle" role="img" aria-label="Brown glitter background for the testimonials spread">
  <div class="blob blob-1"><p>Receiving this award taught me that leadership is service. My captain believed in me before I believed in myself, and every camp, drill and late night planning session shaped who I am today. I hope to pass that same patience and care to the juniors who follow.</p></div>
  <div class="section-title testimonials-title">
    <h2>Testimonials</h2>
    <p class="kicker">Mentoring Quotes</p>
  </div>
  <div class="blob blob-2"><p>Receiving this award taught me that leadership is service. My captain believed in me before I believed in myself, and every camp, drill and late night planning session shaped who I am today. I hope to pass that same patience and care to the juniors who follow.</p></div>
  <div class="blob blob-3"><p>Receiving this award taught me that leadership is service. My captain believed in me before I believed in myself, and every camp, drill and late night planning session shaped who I am today. I hope to pass that same patience and care to the juniors who follow.</p></div>
  <div class="blob blob-4"><p>Receiving this award taught me that leadership is service. My captain believed in me before I believed in myself, and every camp, drill and late night planning session shaped who I am today. I hope to pass that same patience and care to the juniors who follow.</p></div>
</section>

<!-- Recipients spread -->
<section class="spread spread-recipients sparkle" role="img" aria-label="Brown glitter background for the recipients spread">
  <div class="section-title recipients-title">
    <h2>Keystone Award</h2>
    <p class="kicker">Recipients</p>
    <p class="lead">This year we are proud to<br>present the Keystone Award<br>to the following recipients</p>
  </div>

  <div class="company-wrap" style="left:36px;top:262px">
    <div class="company-no">2<small>nd</small></div>
    <div class="company">
      <h3>Singapore Company</h3>
      <p class="unit">Seaview School<br>Riverside Chapel</p>
      <div class="roster">
        <ul><li>SSG Tan Wei Jie Marcus</li><li>SSG Lim Zhi Hao Daniel</li><li>SSG Ivan Koh</li><li>SSG Joel Adrian Santos</li></ul>
        <ul><li>SSG Wong Jun Kai</li><li>SSG Ryan Goh Jiaming</li><li>WO Ng Kah Leong Samuel</li></ul>
      </div>
    </div>
  </div>
  <div class="company-wrap" style="left:36px;top:467px">
    <div class="company-no">5<small>th</small></div>
    <div class="company">
      <h3>Singapore Company</h3>
      <p class="unit">Seaview School<br>Riverside Chapel</p>
      <div class="roster">
        <ul><li>SSG Tan Wei Jie Marcus</li><li>SSG Lim Zhi Hao Daniel</li><li>SSG Ivan Koh</li><li>SSG Joel Adrian Santos</li></ul>
        <ul><li>SSG Wong Jun Kai</li><li>SSG Ryan Goh Jiaming</li><li>WO Ng Kah Leong Samuel</li></ul>
      </div>
    </div>
  </div>
  <div class="company-wrap" style="left:36px;top:672px">
    <div class="company-no">7<small>th</small></div>
    <div class="company">
      <h3>Singapore Company</h3>
      <p class="unit">Seaview School<br>Riverside Chapel</p>
      <div class="roster">
        <ul><li>SSG Tan Wei Jie Marcus</li><li>SSG Lim Zhi Hao Daniel</li><li>SSG Ivan Koh</li><li>SSG Joel Adrian Santos</li></ul>
        <ul><li>SSG Wong Jun Kai</li><li>SSG Ryan Goh Jiaming</li><li>WO Ng Kah Leong Samuel</li></ul>
      </div>
    </div>
  </div>

  <div class="company-wrap" style="left:430px;top:52px">
    <div class="company-no">10<small>th</small></div>
    <div class="company">
      <h3>Singapore Company</h3>
      <p class="unit">Seaview School<br>Riverside Chapel</p>
      <div class="roster">
        <ul><li>SSG Tan Wei Jie Marcus</li><li>SSG Lim Zhi Hao Daniel</li><li>SSG Ivan Koh</li><li>SSG Joel Adrian Santos</li></ul>
        <ul><li>SSG Wong Jun Kai</li><li>SSG Ryan Goh Jiaming</li><li>WO Ng Kah Leong Samuel</li></ul>
      </div>
    </div>
  </div>
  <div class="company-wrap" style="left:430px;top:262px">
    <div class="company-no">12<small>th</small></div>
    <div class="company">
      <h3>Singapore Company</h3>
      <p class="unit">Seaview School<br>Riverside Chapel</p>
      <div class="roster">
        <ul><li>SSG Tan Wei Jie Marcus</li><li>SSG Lim Zhi Hao Daniel</li><li>SSG Ivan Koh</li><li>SSG Joel Adrian Santos</li></ul>
        <ul><li>SSG Wong Jun Kai</li><li>SSG Ryan Goh Jiaming</li><li>WO Ng Kah Leong Samuel</li></ul>
      </div>
    </div>
  </div>
  <div class="company-wrap" style="left:430px;top:467px">
    <div class="company-no">13<small>th</small></div>
    <div class="company">
      <h3>Singapore Company</h3>
      <p class="unit">Seaview School<br>Riverside Chapel</p>
      <div class="roster">
        <ul><li>SSG Tan Wei Jie Marcus</li><li>SSG Lim Zhi Hao Daniel</li><li>SSG Ivan Koh</li><li>SSG Joel Adrian Santos</li></ul>
        <ul><li>SSG Wong Jun Kai</li><li>SSG Ryan Goh Jiaming</li><li>WO Ng Kah Leong Samuel</li></ul>
      </div>
    </div>
  </div>
  <div class="company-wrap" style="left:430px;top:672px">
    <div class="company-no">14<small>th</small></div>
    <div class="company">
      <h3>Singapore Company</h3>
      <p class="unit">Seaview School<br>Riverside Chapel</p>
      <div class="roster">
        <ul><li>SSG Tan Wei Jie Marcus</li><li>SSG Lim Zhi Hao Daniel</li><li>SSG Ivan Koh</li><li>SSG Joel Adrian Santos</li></ul>
        <ul><li>SSG Wong Jun Kai</li><li>SSG Ryan Goh Jiaming</li><li>WO Ng Kah Leong Samuel</li></ul>
      </div>
    </div>
  </div>
</section>

<!-- Back cover -->
<section class="cover back-cover sparkle" role="img" aria-label="Back cover with brown glitter background and sweeping gold curves">
  <svg class="waves" width="380" height="798" viewBox="0 0 380 798" aria-hidden="true">
    <path d="M380 150 Q120 330 60 798 L380 798 Z" fill="var(--gold-deep)"/>
    <path d="M380 230 Q170 390 130 798 L380 798 Z" fill="var(--gold)"/>
    <path d="M380 330 Q240 460 230 798 L380 798 Z" fill="var(--gold-light)" opacity=".6"/>
    <path d="M0 560 Q150 600 380 500 L380 798 L0 798 Z" fill="var(--gold)" opacity=".85"/>
  </svg>
  <div class="tilt back-contact">
    <div class="brand"><span class="brand-dot"></span><span class="brand-name">The Harbour Crew</span></div>
    <p>28 Harbour Lane,<br>Singapore 100001<br>Tel: (65) 6000 1234<br>Fax: (65) 6000 5678<br>Email: hello@harbourcrew.example</p>
  </div>
</section>

</body>
</html>
```